Weightloss company needs Business Card

We want a business card that is clean and professional, yet portrays that we are a friendly, innovative, and versatile program designed to fit the needs of our clients.
I would like there to be 2 sides, one side having an appointment card, and the other side containing the logo and business information. There can be decorations on both sides. The logo is attached.

Target Market(s)

Men and women 40-60

Industry/Entity Type

Business

Contact Information for Business Card

Font styles to use
Sans Serif

Requirements
Must have
• The logo, space for business information
Nice to have
• The colors in the logo
Should not have
• No pictures of people or food

```html
<!DOCTYPE html>
<html lang="en">
<head>
<meta charset="utf-8">
<title>Renew Turn Wellness – Business Card</title>
<link href="https://fonts.googleapis.com/css2?family=PT+Sans:wght@400;700&display=swap" rel="stylesheet">
<style>
  :root {
    --backdrop: #2b2c2e;
    --card: #ffffff;
    --brand-red: #e3203b;
    --brand-blue: #4fc6ee;
    --faint-blue: #e9f6fc;
    --faint-red: #fbe3e6;
    --ink: #1d1d1f;
    --rule: #3a3a3a;
  }
  * { box-sizing: border-box; margin: 0; padding: 0; }
  html, body {
    width: 1200px; height: 900px; overflow: hidden;
    background: var(--backdrop);
    font-family: "PT Sans", Arial, sans-serif;
  }
  .sheet {
    width: 1200px; height: 900px;
    display: flex; flex-direction: column; align-items: center; justify-content: center;
    gap: 40px;
  }
  .card {
    position: relative;
    width: 700px; height: 400px;
    background: var(--card);
    border-radius: 24px;
    overflow: hidden;
  }
  .card svg.deco { position: absolute; inset: 0; }
  .brand-name {
    position: absolute;
    color: var(--brand-red);
    font-weight: 700;
    font-size: 34px;
    line-height: 1;
    white-space: nowrap;
  }

  /* Appointment side */
  .appointment-title {
    position: absolute; left: 56px; top: 96px;
    color: var(--brand-red); font-size: 17px; letter-spacing: .5px;
  }
  .field {
    position: absolute; left: 78px;
    display: flex; align-items: flex-end; gap: 8px;
    font-size: 17px; color: var(--ink);
  }
  .field .blank { border-bottom: 1.5px solid var(--rule); height: 1px; }
  .top-rule { position: absolute; left: 300px; top: 62px; width: 300px; border-top: 1.5px solid var(--rule); }
  .appointment .brand-name { right: 60px; top: 205px; }

  /* Contact side */
  .person-name {
    position: absolute; left: 40px; top: 52px;
    color: var(--brand-red); font-size: 26px; letter-spacing: .5px;
  }
  .person-role {
    position: absolute; left: 42px; top: 86px;
    color: var(--brand-blue); font-size: 15px; letter-spacing: 1px;
  }
  .name-rule { position: absolute; left: 238px; top: 78px; width: 424px; border-top: 1.5px solid var(--rule); }
  .contact .brand-name { right: 56px; top: 150px; }
  .address {
    position: absolute; right: 36px; top: 258px;
    text-align: right; font-size: 17px; line-height: 1.3; color: var(--ink);
  }
  .contact-list {
    position: absolute; left: 40px; top: 292px;
    list-style: none; font-size: 18px; color: var(--ink); line-height: 1.45;
  }
  .contact-list li { display: flex; align-items: center; gap: 12px; }
  .contact-list svg { width: 14px; height: 14px; flex: none; }
</style>
</head>
<body>
<main class="sheet">

  <section class="card appointment" aria-label="Appointment side">
    <svg class="deco" width="700" height="400" viewBox="0 0 700 400" aria-hidden="true">
      <circle cx="420" cy="190" r="150" fill="none" stroke="var(--faint-red)" stroke-width="12"/>
    </svg>
    <div class="top-rule"></div>
    <p class="appointment-title">APPOINTMENT</p>
    <div class="field" style="top:130px"><span>Name:</span><span class="blank" style="width:380px"></span></div>
    <div class="field" style="top:180px"><span>Date:</span><span class="blank" style="width:300px"></span></div>
    <div class="field" style="top:230px"><span>Time:</span><span class="blank" style="width:260px"></span></div>
    <p class="brand-name">Renew Turn Wellness</p>
  </section>

  <section class="card contact" aria-label="Contact side">
    <svg class="deco" width="700" height="400" viewBox="0 0 700 400" aria-hidden="true">
      <circle cx="200" cy="250" r="130" fill="none" stroke="var(--faint-blue)" stroke-width="16"/>
      <rect x="430" y="232" width="270" height="168" fill="var(--brand-blue)"/>
      <circle cx="420" cy="360" r="100" fill="var(--card)"/>
      <path d="M 420 260 A 100 100 0 0 1 500 400" fill="none" stroke="var(--brand-red)" stroke-width="4"/>
    </svg>
    <p class="person-name">MARCUS BELL</p>
    <div class="name-rule"></div>
    <p class="person-role">DIRECTOR</p>
    <p class="brand-name">Renew Turn Wellness</p>
    <p class="address">Cedar Road, 21430<br>Westbay, Newland</p>
    <ul class="contact-list">
      <li>
        <svg viewBox="0 0 16 16" aria-hidden="true"><path d="M3 1l3 3-1.5 2a9 9 0 0 0 5.5 5.5L12 10l3 3-2 2C7 15 1 9 1 3z" fill="var(--brand-red)"/></svg>
        +330 2460-1187
      </li>
      <li>
        <svg viewBox="0 0 16 16" aria-hidden="true"><rect x="1" y="3" width="14" height="10" fill="none" stroke="var(--brand-red)" stroke-width="1.6"/><path d="M1 3l7 6 7-6" fill="none" stroke="var(--brand-red)" stroke-width="1.6"/></svg>
        info@renewturnwellness.com
      </li>
      <li>
        <svg viewBox="0 0 16 16" aria-hidden="true"><circle cx="8" cy="8" r="6.5" fill="none" stroke="var(--brand-red)" stroke-width="1.4"/><path d="M1.5 8h13M8 1.5c3 3 3 10 0 13M8 1.5c-3 3-3 10 0 13" fill="none" stroke="var(--brand-red)" stroke-width="1.2"/></svg>
        www.renewturnwellness.com
      </li>
    </ul>
  </section>

</main>
</body>
</html>
```